Accountability Project Graphics

I want to create 10 social media graphics (new Instagram size 4:5 (1080 x 1350 pixels) focusing on our Quilvo Accountability App, using any of the 3 pictures attached. Use the attached pics only, NO RANDOM STOCK PHOTOGRAPHY. For the color scheme, use the landing page colors/fonts (attached).
You can add any of the 3 photos attached but I mainly need BOLD text that includes these headlines and sub-headlines on them.
Please NOTE for all the headlines below, also add this sub-headline on each graphic:
Stay Consistent with RT in Your Pocket!
Here are the headlines:
• Stop Starting Over Every Monday
• You don't need more willpower. You need more support
• Built for women who are tired of doing this alone
• When Motivation Fades, RT Checks In
• The Support System You've Been Missing
• Support When Motivation Disappears
• What if RT Checked in Every Day?
• The Missing Piece Isn't Another Diet
• Eat the food you love. Stay accountable every day.
• One Bad Meal Doesn't Mean You Failed
women over 40 trying to lose weight

```html
<!DOCTYPE html>
<html lang="en">
<head>
<meta charset="utf-8">
<title>Accountability App Social Graphics</title>
<link rel="stylesheet" href="https://fonts.googleapis.com/css2?family=Libre+Caslon+Text:ital,wght@0,700;1,700&family=Inter:wght@700&display=swap">
<style>
  :root {
    --page: #ffffff;
    --frame-dark: #2e0d2c;
    --frame-mid: #6a1a4a;
    --frame-light: #b32b63;
    --panel: #fcf0f1;
    --panel-shade: #f6dde2;
    --ink: #1d1230;
    --accent: #c8286a;
    --blob-top: #f5d9f2;
    --blob-bottom: #d58ad8;
    --photo-dark: #2a2230;
    --photo-skin: #a56a4f;
  }
  * { margin: 0; padding: 0; box-sizing: border-box; }
  html, body { width: 1200px; height: 295px; overflow: hidden; background: var(--page); }
  .strip { position: relative; width: 1200px; height: 295px; }
  .card {
    position: absolute; top: 13px; width: 214px; height: 267px;
    background: linear-gradient(160deg, var(--frame-light) 0%, var(--frame-mid) 45%, var(--frame-dark) 100%);
  }
  .panel {
    position: absolute; left: 11px; top: 9px; right: 11px; bottom: 9px;
    border-radius: 12px; overflow: hidden;
    background: linear-gradient(180deg, #fdf5f6 0%, var(--panel) 55%, var(--panel-shade) 100%);
  }
  .blob { position: absolute; }
  .backdrop { position: absolute; background: var(--panel-shade); }
  .photo { position: absolute; border-radius: 40px 40px 0 0; }
  .photo--solo { background: linear-gradient(180deg, var(--photo-skin) 0%, var(--photo-dark) 35%, #15111c 100%); }
  .photo--pair { background: linear-gradient(160deg, var(--photo-dark) 0%, #5b4a58 40%, #e9e2e6 55%, #2f3650 100%); }
  .photo--hug { background: linear-gradient(150deg, #2b2433 0%, #8d5a4a 40%, #e04a8a 60%, #dff0a8 100%); }
  .headline {
    position: absolute; z-index: 3; white-space: nowrap;
    font-family: "Libre Caslon Text", Georgia, serif; font-weight: 700;
    color: var(--ink); letter-spacing: -0.3px;
  }
  .headline em { font-style: italic; }
  .hl { color: var(--accent); }
  .subhead {
    position: absolute; z-index: 2; white-space: nowrap;
    font-family: "Inter", Arial, sans-serif; font-weight: 700;
    font-size: 8.2px; line-height: 10.2px; color: var(--ink);
  }
</style>
</head>
<body>
<svg width="0" height="0" style="position:absolute">
  <defs>
    <linearGradient id="blob-fill" x1="0" y1="0" x2="0" y2="1">
      <stop offset="0" stop-color="#f5d9f2"/><stop offset="1" stop-color="#d58ad8"/>
    </linearGradient>
  </defs>
</svg>
<main class="strip">

  <section class="card" style="left:16px">
    <div class="panel">
      <svg class="blob" style="left:13px;top:145px" width="66" height="104" viewBox="0 0 66 104">
        <path d="M0 24 A24 24 0 0 1 48 24 L48 50 Q48 70 66 70 L66 104 L20 104 Q0 104 0 84 Z" fill="url(#blob-fill)"/>
      </svg>
      <div class="photo photo--solo" role="img" aria-label="Smiling coach in a black lace top, hand on hip" style="left:66px;top:73px;width:126px;height:176px"></div>
      <h2 class="headline" style="left:10px;top:10px;font-size:21px;line-height:19.5px">Stop <span class="hl">Starting</span><br><span class="hl">Over</span> <em>Every</em><br><em>Monday</em></h2>
      <p class="subhead" style="left:10px;top:86px">Stay Consistent<br>with <span class="hl">RT in Your</span><br><span class="hl">Pocket!</span></p>
    </div>
  </section>

  <section class="card" style="left:256px">
    <div class="panel">
      <svg class="blob" style="left:13px;top:145px" width="66" height="104" viewBox="0 0 66 104">
        <path d="M0 24 A24 24 0 0 1 48 24 L48 50 Q48 70 66 70 L66 104 L20 104 Q0 104 0 84 Z" fill="url(#blob-fill)"/>
      </svg>
      <div class="photo photo--hug" role="img" aria-label="Coach warmly hugging a client" style="left:77px;top:97px;width:115px;height:152px"></div>
      <h2 class="headline" style="left:12px;top:13px;font-size:20.5px;line-height:19.5px">You don't need<br>more <em>willpower.</em><br><span class="hl">You need more</span><br><span class="hl"><em>support</em></span></h2>
      <p class="subhead" style="left:12px;top:109px">Stay Consistent<br>with <span class="hl">RT in</span><br><span class="hl">Your Pocket!</span></p>
    </div>
  </section>

  <section class="card" style="left:496px">
    <div class="panel">
      <div class="backdrop" style="left:82px;top:157px;width:110px;height:92px"></div>
      <svg class="blob" style="left:13px;top:145px" width="66" height="104" viewBox="0 0 66 104">
        <path d="M0 24 A24 24 0 0 1 48 24 L48 50 Q48 70 66 70 L66 104 L20 104 Q0 104 0 84 Z" fill="url(#blob-fill)"/>
      </svg>
      <div class="photo photo--solo" role="img" aria-label="Coach standing in a black outfit, hand on hip" style="left:116px;top:6px;width:76px;height:243px"></div>
      <h2 class="headline" style="left:10px;top:17px;font-size:23px;line-height:24px">Support<br><span class="hl">When</span><br><span class="hl">Motivation</span><br><span class="hl"><em>Disappears</em></span></h2>
      <p class="subhead" style="left:10px;top:130px">Stay Consistent with<br><span class="hl">RT in&nbsp; Your Pocket!</span></p>
    </div>
  </section>

  <section class="card" style="left:736px">
    <div class="panel">
      <svg class="blob" style="left:13px;top:145px" width="66" height="104" viewBox="0 0 66 104">
        <path d="M0 24 A24 24 0 0 1 48 24 L48 50 Q48 70 66 70 L66 104 L20 104 Q0 104 0 84 Z" fill="url(#blob-fill)"/>
      </svg>
      <div class="photo photo--pair" role="img" aria-label="Coach laughing together with a client on stage" style="left:76px;top:90px;width:116px;height:159px"></div>
      <h2 class="headline" style="left:13px;top:19px;font-size:22px;line-height:24px">The Support<br>System <span class="hl">You've</span><br><span class="hl">Been <em>Missing</em></span></h2>
      <p class="subhead" style="left:13px;top:113px">Stay Consistent<br>with <span class="hl">RT in</span><br><span class="hl">Your Pocket!</span></p>
    </div>
  </section>

  <section class="card" style="left:976px">
    <div class="panel">
      <svg class="blob" style="left:13px;top:145px" width="66" height="104" viewBox="0 0 66 104">
        <path d="M0 24 A24 24 0 0 1 48 24 L48 50 Q48 70 66 70 L66 104 L20 104 Q0 104 0 84 Z" fill="url(#blob-fill)"/>
      </svg>
      <div class="photo photo--solo" role="img" aria-label="Smiling coach in a black lace top, hand on hip" style="left:62px;top:118px;width:94px;height:131px"></div>
      <h2 class="headline" style="left:13px;top:19px;font-size:19px;line-height:24px">Built for women<br><span class="hl">who are tired of</span><br><span class="hl">doing this <em>alone</em></span></h2>
      <p class="subhead" style="left:14px;top:104px">Stay Consistent with <span class="hl">RT in&nbsp; Your Pocket!</span></p>
    </div>
  </section>

</main>
</body>
</html>
```